Custom Cabinet Shop Needs a website design

Hi,
We need a website for a Custom Cabinet Shop and Cabinet parts manufacturing business.
The business has two sides to it. One side provides custom Kitchens, vanities, entertainment units, offices and what not to homeowners and contractors.
The 2nd side of the business provides built to order cabinet boxes and other parts required to put together a project to other cabinet shops, small contractors looking to install there own cabinets.
Website will need a Gallery to display work.
Color scheme to go well with logo.
current website is www.brambleoakcustomcabinets.com
being changed to www.brambleoak.ca
Logo Included in attached files.
Tagline "Joinery with Spirit"
Mission Statement "Our passion is to deliver inspired cabinetry solutions to suit all your needs, supported by our phenomenal star class customer service"
The website should convey quality and professionalism.
Thank you.
Homeowners/ Contractors
Entertainment

```html
<!DOCTYPE html>
<html lang="en">
<head>
<meta charset="utf-8">
<title>Bramble Oak Custom Cabinets</title>
<link href="https://fonts.googleapis.com/css2?family=Cinzel:wght@400&family=Lato:ital,wght@0,300;0,400;0,700;1,300&family=Roboto:wght@300&display=swap" rel="stylesheet">
<style>
:root{
  --orange:#e8582a;
  --ink:#222;
  --muted:#8a8a8a;
  --rule:#cfcfcf;
  --light:#f2f2f2;
  --footer:#151515;
  --footer-text:#b5b5b5;
  --bar:#d9d9d9;
  --white:#fff;
}
*{margin:0;padding:0;box-sizing:border-box}
html,body{width:684px;height:1200px;overflow:hidden}
body{position:relative;font-family:'Lato',sans-serif;color:var(--ink);background:var(--white)}
.abs{position:absolute}

/* hero */
.hero{left:0;top:0;width:684px;height:442px;overflow:hidden}
.hero-photo{left:0;top:0;width:684px;height:442px;
  background:radial-gradient(ellipse at 55% 45%,#6b5444 0%,#3e342d 40%,#1f1d1c 80%)}
.topband{left:0;top:0;width:684px;height:21px;background:#2b2b2b}
.header{left:0;top:21px;width:684px;height:62px;background:rgba(255,255,255,.93)}
.brand{left:32px;top:20px;display:flex;align-items:center;gap:7px;font-family:'Lato',sans-serif;font-weight:700;font-size:15px;letter-spacing:1px;color:var(--ink)}
.brand-dot{width:14px;height:14px;border-radius:50%;background:var(--orange)}
.nav{right:0;top:0;height:62px;display:flex;font-size:7.5px;text-transform:uppercase}
.nav a{display:flex;align-items:center;padding:0 12px;color:var(--ink);text-decoration:none;height:62px}
.nav a.active{background:var(--orange);color:var(--white);padding:0 11px}
.nav a:last-child{padding-right:28px}
.hero-title{left:0;width:684px;top:232px;text-align:center;font-family:'Cinzel',serif;font-size:25px;color:var(--white);letter-spacing:.5px}
.hero-rule{left:274px;top:272px;width:136px;height:1px;background:rgba(255,255,255,.4)}
.hero-sub{left:0;width:684px;top:284px;text-align:center;font-size:9px;color:#e8e8e8;text-transform:uppercase}
.hero-btn{left:310px;top:315px;width:64px;height:22px;border:1px solid rgba(255,255,255,.8);font-size:7px;color:var(--white);display:flex;align-items:center;justify-content:center;text-transform:uppercase}
.arrow{top:243px;width:23px;height:23px;border:1px solid rgba(255,255,255,.8);border-radius:50%}
.arrow.prev{left:30px}.arrow.next{left:634px}

/* section heading */
.sec-head{left:28px;width:630px;display:flex;align-items:center;gap:10px}
.sec-head .line{flex:1;height:1px;background:var(--rule)}
.sec-head h2{font-family:'Roboto',sans-serif;font-weight:300;font-size:19px;color:var(--ink)}
.sec-head h2 span{color:var(--orange)}

.welcome{left:0;top:442px;width:684px;height:160px}
.mission{left:120px;width:444px;top:84px;text-align:center;font-style:italic;font-weight:300;font-size:10px;line-height:14px;color:#333}
.intro{left:100px;width:484px;top:120px;text-align:center;font-weight:300;font-size:7.5px;line-height:13px;color:var(--muted)}

.gallery{left:0;top:602px;width:684px;height:316px;background:var(--light)}
.card{top:80px;width:148px;height:208px;overflow:hidden}
.card-photo{left:0;top:0;width:148px;height:208px}
.card-tab{left:0;bottom:0;width:148px;height:62px}
.card-cap{left:9px;bottom:11px;font-size:6px;color:var(--white);text-transform:uppercase}
.card.open .card-photo{background:var(--orange);opacity:1}
.open-text{left:10px;width:128px;top:71px;text-align:center;color:var(--white);font-size:5.8px;text-transform:uppercase;line-height:7.5px}
.open-text p:first-child{margin-bottom:8px}
.pager{left:638px;top:296px;font-size:12px;color:#555;letter-spacing:4px}

.partners{left:0;top:918px;width:684px;height:86px;display:flex;justify-content:center;align-items:center;gap:22px}
.badge{height:30px;background:#cfcfcf;border-radius:3px}

/* footer */
.footer{left:0;top:1004px;width:684px;height:152px;background:var(--footer)}
.fcol{top:35px}
.fcol h3{font-weight:400;font-size:9.5px;color:var(--orange);text-transform:uppercase;margin-bottom:17px}
.fcol li{list-style:none;font-size:6.5px;color:var(--footer-text);text-transform:uppercase;line-height:13px}
.fcol p{font-size:6.5px;color:var(--footer-text);text-transform:uppercase;line-height:10px}
.field{margin-top:18px;width:121px;height:16px;background:var(--white);font-size:6.3px;color:#333;padding-left:6px;display:flex;align-items:center;text-transform:uppercase}
.sub-btn{margin-top:9px;width:121px;height:18px;background:var(--orange);color:var(--white);font-size:7px;display:flex;align-items:center;justify-content:center;text-transform:uppercase}
.social li{display:flex;align-items:center;gap:9px;line-height:16px}
.social .ico{width:12px;height:12px;border:1px solid var(--footer-text);border-radius:50%}
.loc li{display:flex;gap:10px;align-items:flex-start;line-height:13px}
.loc svg{flex:none;margin-top:1px}

.bottombar{left:0;top:1156px;width:684px;height:44px;background:var(--bar)}
.copy{left:275px;top:18px;font-size:6.5px;color:#444;text-transform:uppercase}
</style>
</head>
<body>

<section class="hero abs">
  <div class="hero-photo abs" role="img" aria-label="Photograph of a dark modern kitchen with a live-edge wood bar counter and stools"></div>
  <div class="topband abs"></div>
  <header class="header abs">
    <div class="brand abs"><span class="brand-dot"></span>BRAMBLE OAK</div>
    <nav class="nav abs">
      <a class="active" href="#">Home</a><a href="#">Gallery</a><a href="#">Services</a><a href="#">Warranty</a><a href="#">Contact</a>
    </nav>
  </header>
  <h1 class="hero-title abs">Joinery with Spirit</h1>
  <div class="hero-rule abs"></div>
  <p class="hero-sub abs">High quality works with proffesional touch</p>
  <div class="hero-btn abs">Know more</div>
  <div class="arrow prev abs"><svg width="21" height="21" viewBox="0 0 21 21"><path d="M12 6.5 8 10.5l4 4" fill="none" stroke="#fff" stroke-width="1.3"/></svg></div>
  <div class="arrow next abs"><svg width="21" height="21" viewBox="0 0 21 21"><path d="M9 6.5l4 4-4 4" fill="none" stroke="#fff" stroke-width="1.3"/></svg></div>
</section>

<section class="welcome abs">
  <div class="sec-head abs" style="top:49px"><span class="line"></span><h2>Welcome to <span>Bramble Oak</span></h2><span class="line"></span></div>
  <p class="mission abs">" Our passion is to deliver inspired cabinetry solutions to suit all your needs, supported by our phenomenal star class customer service "</p>
  <p class="intro abs">Lorem ipsum dolor sit amet Consectetur adipisicing elit, sed do eiusmod tempor incididunt ut labore et dolore magna aliqua. Ut enim ad minim veniam, quis nostrud exercitation ullamco laboris nisi ut aliquip ex ea commodo consequat.</p>
</section>

<section class="gallery abs">
  <div class="sec-head abs" style="top:36px;left:0;width:684px"><span class="line"></span><h2>Our <span>Gallery</span></h2><span class="line"></span></div>

  <div class="card abs" style="left:28px">
    <div class="card-photo abs" role="img" aria-label="Bathroom vanity with dark cabinetry and soaking tub" style="background:linear-gradient(160deg,#b9ab8c,#5a4f47 55%,#2c2825)"></div>
    <svg class="card-tab abs" viewBox="0 0 148 62" preserveAspectRatio="none"><polygon points="0,0 148,46 148,62 0,62" fill="#e8582a" opacity=".93"/></svg>
    <span class="card-cap abs">Lorem ipsum dolor sit amet</span>
  </div>
  <div class="card abs" style="left:189px">
    <div class="card-photo abs" role="img" aria-label="Bright kitchen with white cabinets and pendant light" style="background:linear-gradient(170deg,#e9e5e0,#b7aea6 55%,#4b4744)"></div>
    <svg class="card-tab abs" viewBox="0 0 148 62" preserveAspectRatio="none"><polygon points="0,0 148,46 148,62 0,62" fill="#e8582a" opacity=".93"/></svg>
    <span class="card-cap abs">Lorem ipsum dolor sit amet</span>
  </div>
  <div class="card open abs" style="left:350px">
    <div class="card-photo abs" role="img" aria-label="Kitchen interior under an orange hover overlay"></div>
    <div class="open-text abs"><p>Lorem ipsum dolor sit amet</p><p>Duis aute irure dolor in reprehenderit in voluptate velit esse cillum dolore eu fugiat nulla pariatur.</p></div>
    <svg class="abs" style="left:66px;top:140px" width="16" height="16" viewBox="0 0 16 16"><circle cx="6.5" cy="6.5" r="5" fill="none" stroke="#fff" stroke-width="1.5"/><path d="M10 10l4.5 4.5M4.5 6.5h4M6.5 4.5v4" stroke="#fff" stroke-width="1.5"/></svg>
  </div>
  <div class="card abs" style="left:510px">
    <div class="card-photo abs" role="img" aria-label="Wall of tall dark wood cabinets with recessed handles" style="background:linear-gradient(90deg,#c9c6c2 0%,#3b302c 12%,#2a2320 70%,#cfcac5 100%)"></div>
    <svg class="card-tab abs" viewBox="0 0 148 62" preserveAspectRatio="none"><polygon points="0,0 148,46 148,62 0,62" fill="#e8582a" opacity=".93"/></svg>
    <span class="card-cap abs">Lorem ipsum dolor sit amet</span>
  </div>
  <div class="pager abs">‹›</div>
</section>

<section class="partners abs" aria-label="Partners">
  <span class="badge" style="width:44px"></span>
  <span class="badge" style="width:72px"></span>
  <span class="badge" style="width:68px"></span>
  <span class="badge" style="width:72px"></span>
  <span class="badge" style="width:68px"></span>
  <span class="badge" style="width:72px;height:40px"></span>
</section>

<footer class="footer abs">
  <div class="fcol abs" style="left:28px"><h3>Navigation</h3><ul><li>Home</li><li>Gallery</li><li>Services</li><li>Warranty</li><li>Contacts</li></ul></div>
  <div class="fcol abs" style="left:139px"><h3>Information</h3><ul><li>Privacy policy</li><li>Terms &amp; conditions</li><li>FAQ</li></ul></div>
  <div class="fcol abs" style="left:260px"><h3>Newsletter</h3><p>Subscribe our newsletter to<br>know our daily updates &amp; offer.</p><div class="field">Enter your email id</div><div class="sub-btn">Subscribe</div></div>
  <div class="fcol social abs" style="left:431px"><h3>Follow us</h3><ul><li><span class="ico"></span>Chirpline</li><li><span class="ico"></span>Friendpage</li><li><span class="ico"></span>Workring</li><li><span class="ico"></span>Circlenet</li></ul></div>
  <div class="fcol loc abs" style="left:546px"><h3>Our location</h3><ul>
    <li><svg width="10" height="12" viewBox="0 0 10 12"><path d="M5 11.5S1 7 1 4.5a4 4 0 0 1 8 0C9 7 5 11.5 5 11.5z" fill="none" stroke="#b5b5b5"/><circle cx="5" cy="4.5" r="1.4" fill="#b5b5b5"/></svg><span>214 Larchmere Row,<br>Fenwick, DC 30 KL 12.</span></li>
    <li style="margin-top:12px"><svg width="10" height="10" viewBox="0 0 10 10"><path d="M2 1l2 2-1 1.5c.8 1.5 1.5 2.2 3 3L7.5 6.5l2 2L8 10C4 9.5.5 6 0 2z" fill="#b5b5b5"/></svg><span>Tel: +1 800 555 0142</span></li>
    <li><svg width="10" height="10" viewBox="0 0 10 10"><rect x="1" y="3" width="8" height="5" fill="none" stroke="#b5b5b5"/><rect x="2.5" y="1" width="5" height="2" fill="#b5b5b5"/></svg><span>Fax: +1 800 555 0187</span></li>
  </ul></div>
</footer>

<div class="bottombar abs"><span class="copy abs">Copyrights © 2015. All rights reserved.</span></div>

</body>
</html>
```